Stationery Design Project for Kerbilo, Chicago

Kerbilo, a street parking application which helps car drivers find a street parking spot by offering an ideal path along which to look for parking. This path is calculated by our algorithm based on data (e.g. historical data, baseball games schedule, etc.). Along this path the driver will find a spot and will also save 70% of the search time. Customer we target is reg. between 21 and 45 yo.

We envision something young, fresh, bright and original. Slightly abstract maybe. It should represent the idea and elements of finding street parking in the city, e.g. car(s), parking spot, people, city, etc. (just ideas!).

Logo is attached.

Requirement:
- Business Cards (2 Sided Full Color CMYK)
- Letterhead (1 Sided Full Color CMYK)
- Envelope (1 Sided Full Color CMYK)
- Sticker (1 Sided Full Color CMYK), round with a 2inch diameter.

Reason: We're starting to get more and more designs and need more time to look into all of them. Very exciting!! Thanks to everybody!

Hi all, we're in the process of selecting our favs. Though choices!!! Really good submissions. Will keep you posted and sorry for the delay.

Target Market(s)

Car drivers and owners between 21 and 45

Industry/Entity Type

Parking

Requirements
Must have
• Sticker should be round and include company URL kerbilo.com and the new logo which we will attach soon.
Should not have
• Should not be too serious or boring.

```html
<!DOCTYPE html>
<html lang="en">
<head>
<meta charset="utf-8">
<title>Kerbilo Business Card</title>
<link rel="stylesheet" href="https://fonts.googleapis.com/css2?family=Source+Sans+3:wght@400;600;700&display=swap">
<style>
  :root {
    --page-bg: #e4e4e6;
    --card-white: #ffffff;
    --ink: #1b1b1d;
    --ink-soft: #3a3a3c;
    --rule: #555558;
    --blue: #1a6fc9;
    --blue-deep: #1447a3;
    --blue-light: #2f86dc;
    --white: #ffffff;
  }
  * { box-sizing: border-box; margin: 0; padding: 0; }
  html, body {
    width: 929px; height: 1200px; overflow: hidden;
    background: var(--page-bg);
    font-family: "Source Sans 3", "Myriad Pro", Arial, sans-serif;
  }
  .canvas { position: relative; width: 929px; height: 1200px; }

  .card {
    position: absolute; left: 29px; width: 871px; height: 496px;
    border-radius: 27px; overflow: hidden;
    box-shadow: 0 6px 18px rgba(0,0,0,0.18);
  }
  .card--front { top: 83px; background: var(--card-white); }
  .card--back {
    top: 640px;
    background: linear-gradient(90deg, var(--blue) 0%, var(--blue-light) 45%, var(--blue) 70%, var(--blue-deep) 100%);
  }

  .mark-circle {
    position: absolute; border-radius: 50%;
    background: radial-gradient(circle at 40% 35%, var(--blue-light), var(--blue-deep) 75%);
  }
  .card--front .mark-circle { left: 126px; top: 76px; width: 165px; height: 165px; }
  .card--back .mark-circle { left: 140px; top: 157px; width: 162px; height: 162px; }

  .wordmark {
    position: absolute; color: var(--ink);
    font-weight: 600; font-size: 108px; line-height: 1; letter-spacing: 1px;
  }
  .card--front .wordmark { left: 322px; top: 100px; }
  .card--back .wordmark { left: 332px; top: 185px; }

  .holder {
    position: absolute; left: 0; width: 100%; top: 282px;
    text-align: center; padding-left: 32px; font-size: 22px; color: var(--ink);
  }
  .holder__name { font-weight: 700; font-size: 28px; }
  .holder__role { font-weight: 400; }

  .contact { position: absolute; top: 354px; font-size: 21px; line-height: 35px; color: var(--ink-soft); }
  .contact b { font-weight: 700; color: var(--ink); }
  .contact--phones { left: 50px; }
  .contact--web { left: 276px; }
  .contact--address { left: 561px; top: 364px; line-height: 30px; font-size: 22px; }
  .divider { position: absolute; top: 358px; width: 1px; height: 67px; background: var(--rule); }
  .divider--one { left: 253px; }
  .divider--two { left: 533px; }

  .band { position: absolute; left: 0; bottom: 0; width: 871px; height: 46px; }

  .halo {
    position: absolute; left: 548px; top: 43px; width: 310px; height: 310px; border-radius: 50%;
    background: radial-gradient(circle, rgba(255,255,255,0.12), rgba(255,255,255,0.04) 70%);
  }
  .back-links {
    position: absolute; left: 0; width: 100%; top: 364px;
    text-align: center; padding-left: 60px; font-size: 21px; color: var(--white);
  }
  .back-links b { font-weight: 700; }
</style>
</head>
<body>
<main class="canvas">
  <section class="card card--front">
    <div class="mark-circle"></div>
    <div class="wordmark">Kerbilo</div>
    <p class="holder"><span class="holder__name">Your Name</span> <span class="holder__name">|</span> <span class="holder__role">Designation</span></p>
    <div class="contact contact--phones">
      <p><b>t</b> : 123-456-7890</p>
      <p><b>m</b> : 123-456-7890</p>
    </div>
    <div class="divider divider--one"></div>
    <div class="contact contact--web">
      <p><b>e</b> : name@kerbilo.com</p>
      <p><b>w</b> : www.kerbilo.com</p>
    </div>
    <div class="divider divider--two"></div>
    <div class="contact contact--address">
      <p>Street Name, City Name</p>
      <p>State Name, Country Code</p>
    </div>
    <svg class="band" viewBox="0 0 871 46" preserveAspectRatio="none">
      <defs>
        <linearGradient id="bandDark" x1="0" x2="1">
          <stop offset="0" stop-color="#4a4a4e"/>
          <stop offset="0.6" stop-color="#1e1e20"/>
          <stop offset="1" stop-color="#6a6a6e"/>
        </linearGradient>
        <linearGradient id="bandBlue" x1="0" x2="1">
          <stop offset="0" stop-color="#1447a3"/>
          <stop offset="0.5" stop-color="#1a6fc9"/>
          <stop offset="0.85" stop-color="#2f86dc"/>
          <stop offset="1" stop-color="#1447a3"/>
        </linearGradient>
      </defs>
      <rect x="0" y="0" width="871" height="46" fill="url(#bandBlue)"/>
      <polygon points="0,0 395,0 430,46 0,46" fill="url(#bandDark)"/>
    </svg>
  </section>

  <section class="card card--back">
    <div class="halo"></div>
    <div class="mark-circle"></div>
    <div class="wordmark">Kerbilo</div>
    <p class="back-links"><b>e</b> : name@kerbilo.com | <b>w</b> : www.kerbilo.com</p>
  </section>
</main>
</body>
</html>
```